Start-Up für Training, Coaching & Consulting sucht modernes Webdesign!
Zielgruppe
Wer ist TAVI Training, Coaching & Consulting?
Wir führen Führungskräftetrainings durch, machen Privatkunden für Bewerbungen fit und unterstützen Unternehmen mit Verkaufstrainings. Wir entwickeln Persönlichkeiten im Coaching. Wir beraten Unternehmen und helfen ihnen dabei, ihre Geschäftsabläufe und Prozesse zu optimieren. Dabei steht unsere hohe Qualität im Mittelpunkt - gemeinsam mit unseren kreativen Trainingsmethoden. Unser Background (Diplom-Kaufleute und geprüfte Trainer) bietet dafür die passende Ausgangslage.
Was bedeutet TAVI?
Tavi ist Maori und bdeutet Kreis/Spirale. Er symbolisiert einen wachsenden Silberfarn und steht für persönliche Entwicklung und Entfaltung. Der Tavi ist einerseits unser Namensgeber und unser Logo, andererseits steht der Tavi aber auch für unsere Werte: Denn wir wollen unseren Kunden dabei helfen zu wachsen und sich weiterzuentwickeln - und dies auf eine hochqualitative und seriöse Art und Weise ohne den Eindruck von Esoterik oder Erlebnispädagogik zu vermitteln.
Aufgabenstellung
Modernes Design, das unsere Philosophie widerspiegelt: Wir möchten unseren Kunden auf seriöse und hochqualitative Weise weiterentwickeln. Wir stehen für nachhaltigen Lernerfolg, kreative Trainingsmethoden, Abwechslung, Spaß am Lernen, Qualität, Kompetenz, Fachwissen und Dynamik.
Layout:
1) Header: QMSR geprüfter Trainer, Menüpunkte (siehe Architektur)
2) Banner
3) 3 Teaser (Training, Coaching, Consulting) + Header + 2-3 Zeilen Text (+Icons)
>>> Sichtbarer Bereich auf Homepage: Menü, Banner, Teaser
4) "Warum Sie uns wählen sollten": 5 bullet points ohne weiteren Text
5) "Aus unserem Blog": Frame für 3 Blogartikel + Bild + Datum + Header + 2-3 Zeilen Text
6) Alle drei QMSR Logos
7) Footer: Click Us (quick links), Contact Us (Adresse), Follow Us (Pinnwald, ZOLP, Kontaktor)
8) Copyright + Impressum
>>> Das Design soll klar sein, aber nicht zu kantig. Vielmehr sollen abgerundete Ecken und dynamische Elemente genutzt werden.
Architektur:
3 Ebenen:
1) Homepage
2) TAVI, Training, Coaching, Consulting, für Trainer, Kundenstimmen/Referenzen, Kontakt
3) noch zu bestimmende Produktdetailseiten
Texte werden noch erstellt, Layout kann ggf. mit Platzhaltertext gefüllt werden.
Bildmaterial: Logo und vorhandenes Imagebild werden zur Verfügung gestellt. Bilder können ggf. gekauft werden. Vorschläge erwünscht.
Corporate colors:
grün: #a2c61b + monochromatic colors
http://www.tintoskop.de/a2c61b
grau: #474747 + monochromatic colors
http://www.tintoskop.de/474747

```html
<!DOCTYPE html>
<html lang="de">
<head>
<meta charset="utf-8">
<title>TAVI Training, Coaching & Consulting</title>
<link href="https://fonts.googleapis.com/css2?family=Dosis:wght@400;500;600&display=swap" rel="stylesheet">
<style>
:root{
  --green:#a2c61b;
  --green-dark:#8aab12;
  --grey:#474747;
  --grey-dark:#2a2a2a;
  --text:#333;
  --line:#cfcfcf;
  --white:#fff;
}
*{margin:0;padding:0;box-sizing:border-box}
html,body{width:721px;height:1200px;overflow:hidden;background:var(--white)}
body{font-family:"Dosis",sans-serif;color:var(--text);position:relative}
.abs{position:absolute}
.hero{left:0;top:0;width:721px;height:300px;background:radial-gradient(ellipse at 62% 40%,#b8dc6a 0%,#6fa52c 35%,#3d6e1c 70%,#24461a 100%)}
.hero-title{left:73px;top:128px;font-size:22px;font-weight:500;line-height:1.15;color:var(--white);width:320px}
.hero-sub{left:74px;top:193px;font-size:12.5px;font-weight:500;line-height:1.15;color:var(--white);width:230px}
.hero-arrow{top:158px;width:24px;height:26px}
.header{left:21px;top:4px;width:679px;height:59px;background:var(--white);border-radius:8px}
.brand{left:25px;top:17px;display:flex;align-items:center;gap:5px;font-size:19px;font-weight:600;color:var(--grey)}
.brand-dot{width:11px;height:11px;border-radius:50%;background:var(--green)}
.nav{left:160px;top:27px;display:flex;font-size:11px;color:var(--grey)}
.nav span{position:absolute;white-space:nowrap}
.nav .active{color:var(--green)}
.nav .chev{color:var(--green);font-size:8px}
.badge{left:590px;top:25px;width:58px;height:16px;background:#1f69b1;border-radius:2px}
.welcome{left:0;top:320px;width:721px;text-align:center}
.welcome h1{font-size:18px;font-weight:500;color:var(--green)}
.welcome p{font-size:9.5px;color:var(--green);margin-top:3px}
.card{top:375px;width:219px}
.card-img{width:219px;height:121px;border:3px solid var(--green)}
.card-icon{position:absolute;left:85px;top:89px;width:48px;height:48px;border-radius:50%;background:var(--white);border:3px solid var(--green);display:flex;align-items:center;justify-content:center}
.card h2{margin-top:30px;text-align:center;font-size:13px;font-weight:500;color:var(--green);letter-spacing:.3px}
.card p{margin-top:7px;text-align:center;font-size:7.6px;line-height:1.35;color:var(--text)}
.btn{display:block;margin:12px auto 0;width:69px;height:21px;line-height:21px;text-align:center;background:var(--green);color:var(--white);font-size:10px;border-radius:2px}
.rule{left:21px;width:679px;height:1px;background:var(--line)}
.rule.green{background:#c7d98c}
.vrule{left:360px;top:675px;width:1px;height:210px;background:var(--line)}
.sec-title{font-size:13px;font-weight:500;color:var(--grey)}
.why{left:21px;top:682px;width:280px}
.why p{margin-top:6px;font-size:7.6px;line-height:1.35}
.bullets{left:58px;top:759px;list-style:none}
.bullets li{font-size:10px;color:var(--green);height:24.3px}
.bullets li::before{content:"• "}
.blog{left:404px;top:682px;width:280px}
.post{position:absolute;left:404px;width:290px;height:42px}
.post-img{position:absolute;left:0;top:0;width:53px;height:41px;border-radius:8px;background:linear-gradient(135deg,#9fb4c4,#e5d6c0 60%,#c9a07a)}
.post-body{position:absolute;left:66px;top:1px}
.post-date{font-size:8.5px;color:var(--green)}
.post-title{font-size:8.5px;color:var(--grey)}
.post-text{font-size:6.3px;line-height:1.35;margin-top:3px;width:200px}
.partner{top:956px;height:30px;background:#1f69b1;border-radius:2px}
.footer{left:0;top:990px;width:721px;height:210px}
.footer-brand{left:27px;top:1058px;display:flex;align-items:center;gap:4px;font-size:16px;font-weight:600;color:var(--white)}
.fcol{top:1063px;font-size:8px;color:var(--white);line-height:1.3}
.fcol h3{font-size:9px;font-weight:600;margin-bottom:11px}
.social{display:flex;gap:8px}
.social span{width:15px;height:15px;border-radius:50%;background:var(--green)}
.copy{left:29px;top:1176px;font-size:8.5px;color:var(--white)}
</style>
</head>
<body>

<div class="abs hero" role="img" aria-label="Foto: sich entrollender Farnwedel vor grünem, unscharfem Hintergrund"></div>
<div class="abs hero-title">Nachhaltiger Lernerfolg durch kreative Trainingsmethoden</div>
<div class="abs hero-sub">Wir helfen Ihnen dabei zu wachsen und sich weiterzuentwickeln</div>
<svg class="abs hero-arrow" style="left:20px" viewBox="0 0 24 26"><path d="M17 2 6 13l11 11" fill="none" stroke="#e8e8e8" stroke-width="5"/></svg>
<svg class="abs hero-arrow" style="left:677px" viewBox="0 0 24 26"><path d="M7 2l11 11L7 24" fill="none" stroke="#e8e8e8" stroke-width="5"/></svg>

<header class="abs header">
  <div class="abs brand"><span>TAVI</span><span class="brand-dot"></span></div>
  <nav class="abs nav">
    <span class="active" style="left:0">Startseite</span>
    <span style="left:81px">Leistungen <span class="chev">&#9660;</span></span>
    <span style="left:166px">Für Trainer <span class="chev">&#9660;</span></span>
    <span style="left:250px">Referenzen</span>
    <span style="left:338px">Kontakt</span>
  </nav>
  <div class="abs badge" role="img" aria-label="Partnerabzeichen geprüfter Trainer"></div>
</header>

<section class="abs welcome">
  <h1>Willkommen auf TAVI</h1>
  <p>Lorem ipsum dolor sit amet, consetetur sadipscing elitr</p>
</section>

<article class="abs card" style="left:22px">
  <div class="card-img" role="img" aria-label="Foto: Trainer mit Tablet im Gespräch" style="background:linear-gradient(120deg,#6b4a3a,#c7b2a0 50%,#8c5d48)"></div>
  <div class="card-icon"><svg width="22" height="22" viewBox="0 0 22 22"><circle cx="10" cy="6" r="5" fill="#111"/><path d="M2 21c0-6 4-9 8-9s8 3 8 9z" fill="#111"/><path d="M17 15v6M14 18h6" stroke="#111" stroke-width="1.5"/></svg></div>
  <h2>TRAINING</h2>
  <p>Lorem ipsum dolor sit amet, consetetur sadipscing elitr,<br>sed diam nonumy eirmod tempor invidunt ut labore et<br>dolore magna aliquyam erat, sed diam voluptua.</p>
  <span class="btn">Mehr</span>
</article>
<article class="abs card" style="left:251px">
  <div class="card-img" role="img" aria-label="Foto: Hände mit Tablet und Stift am Schreibtisch" style="background:linear-gradient(120deg,#b7c6d4,#eef1f4 50%,#c9d3dc)"></div>
  <div class="card-icon"><svg width="24" height="22" viewBox="0 0 24 22"><rect x="10" y="2" width="12" height="9" fill="none" stroke="#111" stroke-width="1.3"/><circle cx="6" cy="5" r="2.5" fill="#111"/><rect x="4" y="8" width="4" height="8" fill="#111"/><circle cx="12" cy="15" r="2" fill="#111"/><circle cx="18" cy="15" r="2" fill="#111"/><rect x="2" y="18" width="20" height="3" fill="#111"/></svg></div>
  <h2>COACHING</h2>
  <p>Lorem ipsum dolor sit amet, consetetur sadipscing elitr,<br>sed diam nonumy eirmod tempor invidunt ut labore et<br>dolore magna aliquyam erat, sed diam voluptua.</p>
  <span class="btn">Mehr</span>
</article>
<article class="abs card" style="left:481px">
  <div class="card-img" role="img" aria-label="Foto: Beraterin im Gespräch mit einer Gruppe" style="background:linear-gradient(120deg,#6d8aa6,#d9cdb8 50%,#9bb2c6)"></div>
  <div class="card-icon"><svg width="24" height="22" viewBox="0 0 24 22"><circle cx="7" cy="7" r="4" fill="#111"/><path d="M1 20c0-5 3-7 6-7s6 2 6 7z" fill="#111"/><circle cx="17" cy="5" r="3" fill="#111"/><path d="M12 14c0-4 2-6 5-6s5 2 5 6z" fill="#111"/></svg></div>
  <h2>CONSULTING</h2>
  <p>Lorem ipsum dolor sit amet, consetetur sadipscing elitr,<br>sed diam nonumy eirmod tempor invidunt ut labore et<br>dolore magna aliquyam erat, sed diam voluptua.</p>
  <span class="btn">Mehr</span>
</article>

<div class="abs rule" style="top:654px"></div>

<section class="abs why">
  <h2 class="sec-title">Wählen Sie Uns</h2>
  <p>Lorem ipsum dolor sit amet, consetetur sadipscing elitr, sed diam nonumy eirmod tempor invidunt ut labore et dolore magna aliquyam erat, sed diam voluptua. At vero eos et accusam et justo duo dolores et ea rebum.</p>
</section>
<ul class="abs bullets">
  <li>Lorem ipsum dolor sit amet</li>
  <li>Lorem ipsum dolor sit amet</li>
  <li>Lorem ipsum dolor sit amet</li>
  <li>Lorem ipsum dolor sit amet</li>
  <li>Lorem ipsum dolor sit amet</li>
</ul>

<div class="abs vrule"></div>

<section class="abs blog"><h2 class="sec-title">Unser Blog</h2></section>
<div class="post" style="top:713px">
  <div class="post-img" role="img" aria-label="Foto: Seminargruppe"></div>
  <div class="post-body"><div class="post-date">21.12.2015 - 12:48 Uhr</div><div class="post-title">Kreative Trainingsmethoden</div><div class="post-text">Lorem ipsum dolor sit amet, consectetur adipisicing elit, sed do eiusmod tempor incididunt ut labore et dolore magna aliqua.</div></div>
</div>
<div class="post" style="top:774px">
  <div class="post-img" role="img" aria-label="Foto: Seminargruppe"></div>
  <div class="post-body"><div class="post-date">21.12.2015 - 12:48 Uhr</div><div class="post-title">Kreative Trainingsmethoden</div><div class="post-text">Lorem ipsum dolor sit amet, consectetur adipisicing elit, sed do eiusmod tempor incididunt ut labore et dolore magna aliqua.</div></div>
</div>
<div class="post" style="top:834px">
  <div class="post-img" role="img" aria-label="Foto: Seminargruppe"></div>
  <div class="post-body"><div class="post-date">21.12.2015 - 12:48 Uhr</div><div class="post-title">Kreative Trainingsmethoden</div><div class="post-text">Lorem ipsum dolor sit amet, consectetur adipisicing elit, sed do eiusmod tempor incididunt ut labore et dolore magna aliqua.</div></div>
</div>

<div class="abs rule green" style="top:911px"></div>

<div class="abs partner" style="left:195px;top:958px;width:81px;height:22px" role="img" aria-label="Partnerabzeichen geprüfter Business-Trainer"></div>
<div class="abs partner" style="left:335px;top:951px;width:25px;height:32px" role="img" aria-label="Partnerabzeichen Mitglied"></div>
<div class="abs partner" style="left:450px;top:951px;width:26px;height:33px" role="img" aria-label="Partnerabzeichen Berufsverband"></div>

<svg class="abs footer" viewBox="0 0 721 210" preserveAspectRatio="none"><path d="M0 22C180 42 480 40 721 6V210H0z" fill="var(--grey-dark)"/></svg>

<div class="abs footer-brand"><span>TAVI</span></div>
<div class="abs fcol" style="left:240px"><h3>Quicklinks</h3>Startseite<br>Referenzen<br>Kontakt<br>Impressum</div>
<div class="abs fcol" style="left:370px"><h3>Kontakt</h3>TAVI GmbH<br>Am Lindenhang 4b<br>24103 Kiel<br><br>Tel: &nbsp;&nbsp;0431 55 20 718<br>E-Mail: info@tavi-beispiel.de</div>
<div class="abs fcol" style="left:495px"><h3>Folgen</h3>
  <div class="social"><span aria-label="Pinnwald"></span><span aria-label="Kontaktor"></span><span aria-label="ZOLP"></span></div>
</div>
<div class="abs copy">© Copyright 2001-2016 - All Rights Reserved</div>

</body>
</html>
```